KRT Project Signage

Need a sign to be displayed in the front of properties currently under Construction or Renovation to advertise our company information. Need it to be Professional and Contemporary. We are a Design/Build Construction Company. Information should include Company Name, email, website, phone number. Attached: Logo and company brochure, also included and inspiration images

```html
<!DOCTYPE html>
<html lang="en">
<head>
<meta charset="UTF-8">
<title>KRT Project Signage</title>
<link rel="stylesheet" href="https://fonts.googleapis.com/css2?family=League+Spartan:wght@600;700&family=Poppins:wght@400;600;700&display=swap">
<style>
  :root {
    --ink: #242424;
    --navy-ink: #0f1f24;
    --sun: #f2ea47;
    --paper: #ffffff;
    --backdrop: #bdbdbd;
  }
  * { margin: 0; padding: 0; box-sizing: border-box; }
  html, body { width: 800px; height: 1200px; overflow: hidden; background: var(--backdrop); }
  .sign {
    position: relative;
    width: 800px;
    height: 1200px;
    background: var(--paper);
    overflow: hidden;
  }
  .sign__dark-field {
    position: absolute; left: 0; top: 0;
    width: 800px; height: 705px;
    background: var(--ink);
  }
  .name-banner {
    position: absolute; left: 0; top: 39px;
    width: 730px; height: 335px;
    background: var(--sun);
    border-radius: 0 168px 168px 0;
  }
  .name-banner__name {
    position: absolute; left: 80px; top: 58px;
    font-family: "League Spartan", sans-serif;
    font-weight: 700;
    font-size: 112px;
    line-height: 94px;
    color: var(--navy-ink);
    letter-spacing: -1px;
  }
  .name-banner__role {
    position: absolute; left: 84px; top: 252px;
    font-family: "League Spartan", sans-serif;
    font-weight: 600;
    font-size: 36px;
    letter-spacing: 10px;
    color: var(--navy-ink);
  }
  .contact {
    position: absolute; left: 0; top: 0;
    font-family: "Poppins", sans-serif;
    color: var(--paper);
    font-size: 38px;
  }
  .contact__line { position: absolute; left: 131px; white-space: nowrap; line-height: 1; }
  .contact__icon { position: absolute; }
  .office-bar {
    position: absolute; left: 76px; top: 669px;
    width: 653px; height: 70px;
    background: var(--sun);
    border-radius: 35px;
  }
  .office-bar__label {
    position: absolute; left: 10px; top: 9px;
    width: 222px; height: 52px;
    background: var(--ink);
    border-radius: 26px;
    color: var(--paper);
    font-family: "Poppins", sans-serif;
    font-weight: 700;
    font-size: 38px;
    line-height: 54px;
    text-align: center;
  }
  .office-bar__icon { position: absolute; left: 248px; top: 9px; }
  .office-bar__number {
    position: absolute; left: 322px; top: 8px;
    font-family: "Poppins", sans-serif;
    font-weight: 700;
    font-size: 46px;
    line-height: 58px;
    letter-spacing: 3px;
    color: var(--navy-ink);
  }
  .direct-line__icon { position: absolute; left: 77px; top: 782px; }
  .direct-line__number {
    position: absolute; left: 163px; top: 774px;
    font-family: "League Spartan", sans-serif;
    font-weight: 700;
    font-size: 112px;
    line-height: 100px;
    letter-spacing: -3px;
    color: var(--ink);
    white-space: nowrap;
  }
  .company-mark {
    position: absolute; left: 0; top: 990px;
    width: 800px;
    display: flex; align-items: center; justify-content: center;
    gap: 18px;
  }
  .company-mark__dot {
    width: 40px; height: 40px;
    border-radius: 50%;
    background: var(--sun);
  }
  .company-mark__name {
    font-family: "League Spartan", sans-serif;
    font-weight: 700;
    font-size: 50px;
    letter-spacing: 2px;
    color: var(--ink);
    text-transform: uppercase;
  }
</style>
</head>
<body>
  <main class="sign">
    <div class="sign__dark-field"></div>

    <section class="name-banner">
      <h1 class="name-banner__name">MARCUS<br>HALE</h1>
      <p class="name-banner__role">DESIGN &amp; BUILDER</p>
    </section>

    <section class="contact">
      <svg class="contact__icon" style="left:78px;top:438px" width="36" height="46" viewBox="0 0 24 32" aria-hidden="true">
        <path d="M12 0C5.4 0 0 5.2 0 11.7 0 20 12 32 12 32s12-12 12-20.3C24 5.2 18.6 0 12 0z" fill="var(--sun)"/>
        <circle cx="12" cy="11.5" r="4.5" fill="var(--ink)"/>
      </svg>
      <p class="contact__line" style="top:448px">1450 Harbor View Rd., Ste. 310</p>
      <p class="contact__line" style="top:498px">Coral Bay, FL 33990</p>
      <svg class="contact__icon" style="left:76px;top:570px" width="38" height="28" viewBox="0 0 38 28" aria-hidden="true">
        <rect x="1.5" y="1.5" width="35" height="25" fill="none" stroke="var(--sun)" stroke-width="3"/>
        <path d="M2 2 L19 16 L36 2 M2 26 L14 12 M36 26 L24 12" fill="none" stroke="var(--sun)" stroke-width="3"/>
      </svg>
      <p class="contact__line" style="top:562px;left:129px">nolan@krtconstruction.com</p>
    </section>

    <div class="office-bar">
      <span class="office-bar__label">OFFICE</span>
      <svg class="office-bar__icon" width="52" height="52" viewBox="0 0 52 52" aria-hidden="true">
        <circle cx="26" cy="26" r="26" fill="var(--ink)"/>
        <path d="M17 14c2-2 4-1 5 1l2 4c1 2 0 3-1 4l-1 1c1 3 4 6 7 7l1-1c1-1 2-2 4-1l4 2c2 1 3 3 1 5-3 3-7 4-12 0-5-3-9-7-11-12-2-4-1-8 1-10z" fill="var(--sun)"/>
        <path d="M29 14a10 10 0 0 1 9 9M29 19a5 5 0 0 1 4 4" fill="none" stroke="var(--sun)" stroke-width="2.4" stroke-linecap="round"/>
      </svg>
      <span class="office-bar__number">555.240.1187</span>
    </div>

    <svg class="direct-line__icon" width="76" height="76" viewBox="0 0 52 52" aria-hidden="true">
      <circle cx="26" cy="26" r="26" fill="var(--sun)"/>
      <path d="M17 14c2-2 4-1 5 1l2 4c1 2 0 3-1 4l-1 1c1 3 4 6 7 7l1-1c1-1 2-2 4-1l4 2c2 1 3 3 1 5-3 3-7 4-12 0-5-3-9-7-11-12-2-4-1-8 1-10z" fill="var(--ink)"/>
      <path d="M29 14a10 10 0 0 1 9 9M29 19a5 5 0 0 1 4 4" fill="none" stroke="var(--ink)" stroke-width="2.4" stroke-linecap="round"/>
    </svg>
    <p class="direct-line__number">555.318.2764</p>

    <footer class="company-mark">
      <span class="company-mark__dot"></span>
      <span class="company-mark__name">KRT Construction</span>
    </footer>
  </main>
</body>
</html>
```